Create an awesome website for a medical clinic

This is a new website for a doctor's office. The site should be clean and modern, easy to navigate.

This is a wellness clinic, we want to help our clients have a healthy, active lifestyle. It should be friendly and inviting, and easy for them to call or schedule an appointment.

The site should be responsive and designed using the attached Bootstrap 3 PSD.

We will provide stock photos, until then please use stock photos from:

pixelharbor.com or
framequarry.com (preferred)

Some example sites of clean and modern designs that we like:

https://tulsaspinecare.com/
http://reachpastjoints.com/
http://turninghealthier.com/

Also attached is a temporary logo you can use.

Reason: Thank you everyone for your great designs - we need a little more time so I'm extending the project.

Need extra days to review

Also, the colors in the new logo I just linked to are the final colors of the logo, so feel free to use any complimentary colors to it.

Hi everyone, The boss wants to change the layout of the site a little bit - here's the revised layout: https://www.filecrate.com/s/k9rt31vx2qp84zn/notes%2011_29_2017.pdf?dl=0 And the graphic assets you can use are here: https://www.filecrate.com/s/k9rt31vx2qp84zn/notes%2011_29_2017.pdf?dl=0 Feel free to change the background color of the "topbar", and change the icons of the "why people trust us" if you want, these are just temporary placeholders. Thanks for your patience and hard work!

Target Market(s)

People seeking medical treatment (wellness clinic)

Industry/Entity Type

Doctor

Number of Pages Required

1 page

Font styles to use
Sans Serif

Colors
0592cd
33a6d7
abd037
9bcb3c

Requirements
Must have
• The home page should have: a strong hero image/slideshow, clinic phone number should be prominent and at the top of the page (in the nav), a "what to expect" section (this is like a FAQs section - see attachment), and a strong call to action (a button to call or schedule an appointment).
• The what to expect section is useful so that prospective clients can determine if we're a good fit for them or not. It's a basic, first-step pre-qualification block of information.
• Social media icons which links to our social media profiles should be included.
Nice to have
• - Link to 3 most recent blog entries
• - Testimonials
• - How a multilevel nav menu looks.

```html
<!DOCTYPE html>
<html lang="en">
<head>
<meta charset="utf-8">
<title>Fernwell Medical Clinic</title>
<link rel="stylesheet" href="https://fonts.googleapis.com/css2?family=Open+Sans:ital,wght@0,400;0,600;0,700;1,400&display=swap">
<style>
:root{
  --blue:#0592cd;
  --blue-light:#33a6d7;
  --blue-pale:#d8eef9;
  --green:#9bcb3c;
  --green-light:#abd037;
  --ink:#222;
  --grey:#555;
  --dark:#1f1f1f;
  --darker:#141414;
  --white:#fff;
}
*{box-sizing:border-box;margin:0;padding:0}
html,body{width:1200px;height:4157px;overflow:hidden}
body{font-family:"Open Sans",Arial,sans-serif;color:var(--ink);background:var(--white);position:relative}
.abs{position:absolute}

/* hero */
.hero{position:absolute;left:0;top:0;width:1200px;height:712px;overflow:hidden}
.hero-photo{position:absolute;inset:0;background:linear-gradient(180deg,#dfe9ec 0%,#c9d8dc 38%,#9aa27a 55%,#6f7a46 75%,#4e5730 100%)}
.topnav{position:absolute;left:0;top:0;width:1200px;height:34px;background:rgba(20,20,20,.78)}
.topnav a{position:absolute;top:0;height:34px;line-height:34px;color:var(--white);font-size:13px;font-weight:600;text-decoration:none;text-align:center;width:118px}
.topnav a.active{background:rgba(0,0,0,.55)}
.burger{position:absolute;left:1135px;top:8px;width:26px;height:18px}
.burger span{display:block;height:3px;background:var(--blue-light);margin-bottom:4px}
.submenu{position:absolute;top:38px;width:112px}
.submenu div{height:26px;line-height:24px;background:var(--blue);border:1px solid var(--white);color:var(--white);font-size:11px;padding-left:10px;margin-bottom:4px;position:relative}
.brand{position:absolute;left:97px;top:0;width:236px;height:212px}
.socials{position:absolute;left:28px;top:5px;display:flex;gap:7px}
.socials i{width:24px;height:24px;border-radius:50%;background:var(--blue);border:2px solid var(--white);display:block}
.brand-phone{position:absolute;left:28px;top:36px;color:var(--white);font-size:20px;line-height:26px;font-weight:700;white-space:nowrap;display:flex;align-items:center;gap:8px}
.brand-card{position:absolute;left:0;top:74px;width:236px;height:134px;background:var(--white);box-shadow:0 3px 8px rgba(0,0,0,.3)}
.brand-card .name{position:absolute;left:18px;top:24px;font-size:40px;line-height:42px;font-weight:700;color:var(--green);letter-spacing:.5px}
.brand-card .sub{position:absolute;left:18px;top:70px;font-size:25px;font-weight:700;color:var(--green)}
.slide-arrow{position:absolute;top:355px;width:30px;height:44px;background:rgba(40,40,40,.75)}
.caption{position:absolute;left:305px;top:430px;width:595px;height:213px;background:rgba(30,30,30,.55);text-align:center;color:var(--white)}
.caption h1{font-size:34px;font-weight:600;margin-top:10px}
.caption p{font-size:24px;line-height:30px;margin:10px 20px 0}
.btn{display:inline-block;background:var(--blue);color:var(--white);font-weight:700;font-size:14px;border-radius:4px;padding:8px 18px;letter-spacing:.5px}
.btn-dark{background:#2b2b2b;border:1px solid #777;font-size:13px;margin-top:10px}
.dots{position:absolute;left:566px;top:668px;display:flex;gap:10px}
.dots i{width:10px;height:10px;border-radius:50%;background:rgba(255,255,255,.6);display:block}
.dots i:first-child{background:var(--white)}

/* concern wheel */
.concerns{position:absolute;left:0;top:712px;width:1200px;height:1436px}
.ready{position:absolute;left:69px;top:959px;width:1059px;height:413px;background:rgba(255,255,255,.9);padding:22px 60px 0}
.ready h2{text-align:center;color:var(--blue);font-size:32px;font-weight:700}
.rule{width:640px;height:3px;background:var(--blue);margin:6px auto 18px}
.ready p{font-size:15.5px;line-height:20px;color:var(--ink);margin-bottom:14px}
.ready p.quote{border-left:3px solid var(--blue);padding-left:10px}
.ready .cta{text-align:center}

/* what to expect */
.expect{position:absolute;left:0;top:2148px;width:1200px;height:560px}
.expect-band{position:absolute;left:0;top:0;width:1200px;height:249px;background:var(--green-light)}
.expect h2,.blog h2{position:absolute;left:0;width:1200px;text-align:center;font-size:34px;font-weight:700}
.expect h2{top:12px;color:var(--white)}
.expect .rule-w{position:absolute;left:236px;top:66px;width:728px;height:3px;background:var(--white)}
.visit{position:absolute;top:110px;width:236px;height:416px;background:var(--white);box-shadow:0 2px 8px rgba(0,0,0,.25);padding:8px}
.visit .ph{height:250px}
.visit .tag{margin:8px -8px 0 -8px;height:32px;background:var(--green);color:var(--white);font-weight:700;font-size:22px;text-align:center;line-height:32px}
.visit p{font-size:15px;line-height:19px;margin-top:6px;color:var(--ink)}

/* testimonials */
.testimonials{position:absolute;left:69px;top:2757px;width:1059px;height:410px;overflow:hidden}
.testimonials .sea{position:absolute;inset:0;background:linear-gradient(180deg,#4aa7d9 0%,#1f83c4 30%,#0d5f9c 55%,#2d8bc6 100%)}
.testimonials h2{position:absolute;left:0;width:1059px;top:14px;text-align:center;color:var(--white);font-size:34px;font-weight:600}
.testimonials .rule-w{position:absolute;left:330px;top:66px;width:400px;height:2px;background:var(--white)}
.quote-box{position:absolute;left:167px;top:69px;width:734px;height:300px;background:rgba(30,80,130,.55)}
.quote-box p{position:absolute;left:60px;top:18px;width:480px;color:var(--white);font-style:italic;font-size:15.5px;line-height:21px}
.quote-box .who{position:absolute;left:560px;top:260px;color:var(--white);font-style:italic;font-weight:700;font-size:18px}
.portrait{position:absolute;left:560px;top:16px;width:95px;height:95px;border:3px solid var(--white)}
.qmark{position:absolute;font-size:90px;font-weight:700;color:var(--white);line-height:1}
.t-arrow{position:absolute;top:176px;width:34px;height:46px;background:rgba(40,40,40,.6)}

/* blog */
.blog{position:absolute;left:0;top:3200px;width:1200px;height:480px}
.blog h2{top:40px;color:var(--blue)}
.blog .rule-b{position:absolute;left:300px;top:96px;width:600px;height:3px;background:var(--blue)}
.post{position:absolute;top:134px;width:333px;height:332px}
.post .ph{height:177px}
.post .body{height:155px;background:var(--blue);color:var(--white);padding:10px 14px;position:relative}
.post h3{text-align:center;font-size:24px;font-weight:700}
.post p{font-size:15.5px;line-height:19px;margin-top:4px}
.post .more{position:absolute;right:0;bottom:4px;background:var(--green);color:var(--white);font-size:16px;padding:1px 12px}
.b-arrow{position:absolute;top:275px;width:34px;height:46px;background:var(--blue)}

/* footer */
.footer{position:absolute;left:0;top:3755px;width:1200px;height:368px;background:var(--dark);color:#ddd}
.footer h4{position:absolute;top:56px;color:var(--green);font-size:22px;font-weight:700}
.footer .sep{position:absolute;top:38px;width:1px;height:300px;background:#444}
.footer ul{position:absolute;left:104px;top:102px;list-style:none}
.footer li{font-size:17px;line-height:42px;position:relative;padding-left:24px}
.footer li::before{content:"";position:absolute;left:0;top:15px;width:12px;height:12px;border-radius:50%;background:var(--green)}
.contact{position:absolute;left:470px;top:100px;font-size:16px;line-height:22px}
.contact div{position:relative;padding-left:26px;margin-bottom:22px}
.contact svg{position:absolute;left:0;top:2px}
.map{position:absolute;left:795px;top:116px;width:333px;height:111px;background:linear-gradient(135deg,#e6e2d6,#d5dcc8 50%,#e3ddcf)}
.copy{position:absolute;left:0;top:4123px;width:1200px;height:34px;background:var(--darker);color:#aaa;font-size:14px;text-align:center;line-height:34px}
</style>
</head>
<body>

<header class="hero">
  <div class="hero-photo" role="img" aria-label="Woman doing a stretching pose in a wheat field under a pale sky"></div>
  <nav class="topnav">
    <a style="left:388px">Menu Link 1</a>
    <a style="left:506px">Menu Link 2</a>
    <a style="left:624px">Menu Link 3</a>
    <a style="left:742px">Menu Link 4</a>
    <a class="active" style="left:872px">Menu Link 5</a>
    <a style="left:990px">Menu Link 6</a>
    <div class="burger"><span></span><span></span><span></span></div>
  </nav>
  <div class="submenu" style="left:878px">
    <div>Submenu 1</div><div>Submenu 2 ›</div><div>Submenu 3 ›</div>
  </div>
  <div class="submenu" style="left:1000px;top:68px">
    <div>Submenu 2.1</div><div>Submenu 2.2</div><div>Submenu 2.3</div>
  </div>
  <div class="brand">
    <div class="socials"><i></i><i></i><i></i><i></i><i></i></div>
    <div class="brand-phone"><svg width="18" height="18" viewBox="0 0 16 16"><path d="M3 1l3 3-2 2c1 2 3 4 5 5l2-2 3 3-2 3C7 15 1 9 1 3z" fill="#ffffff"/></svg>555 · 018 · 4420</div>
    <div class="brand-card">
      <div class="name">FERNWELL</div>
      <div class="sub">MEDICAL CLINIC</div>
    </div>
  </div>
  <div class="slide-arrow" style="left:0"></div>
  <div class="slide-arrow" style="left:1170px"></div>
  <div class="caption">
    <h1>Lorem Ipsum Dolor</h1>
    <p>Dictumst consectetuer donec mi, vestibulum commodo eget nec in at viverra sociis bibendum. Amet tempor cras vitae, amet et ante.</p>
    <span class="btn btn-dark">SCHEDULE NOW</span>
  </div>
  <div class="dots"><i></i><i></i><i></i></div>
</header>

<section class="concerns">
  <svg class="abs" style="left:0;top:0" width="1200" height="1436" viewBox="0 0 1200 1436">
    <defs>
      <linearGradient id="sweep" x1="0" y1="0" x2="1" y2="1">
        <stop offset="0" stop-color="#e9f5fb"/><stop offset="1" stop-color="#33a6d7"/>
      </linearGradient>
      <radialGradient id="core" cx="50%" cy="40%" r="60%">
        <stop offset="0" stop-color="#33a6d7"/><stop offset="1" stop-color="#0583c0"/>
      </radialGradient>
    </defs>
    <path d="M0 820 C 300 1000, 800 900, 1200 560 L1200 1436 L0 1436 Z" fill="url(#sweep)" opacity=".55"/>
    <path d="M0 1000 C 400 1150, 850 1000, 1200 760 L1200 1436 L0 1436 Z" fill="#33a6d7" opacity=".45"/>
    <g transform="translate(599 466)">
      <circle r="382" fill="#fff"/>
      <g fill="#0592cd">
        <path id="seg" d="M-179.3 -337.3 A382 382 0 0 1 179.3 -337.3 L154.9 -291.4 A330 330 0 0 0 -154.9 -291.4 Z"/>
        <use href="#seg" transform="rotate(60)"/>
        <use href="#seg" transform="rotate(120)"/>
        <use href="#seg" transform="rotate(180)"/>
        <use href="#seg" transform="rotate(240)"/>
        <use href="#seg" transform="rotate(300)"/>
      </g>
      <g fill="#fff" font-family="Open Sans, Arial, sans-serif" font-weight="700" font-size="24" text-anchor="middle">
        <text y="-348">Headache</text>
        <text transform="rotate(60)" y="-348">Headache</text>
        <text transform="rotate(300)" y="-348">Headache</text>
        <text transform="rotate(-60)" y="366">Headache</text>
        <text y="366">Headache</text>
        <text transform="rotate(60)" y="366">Headache</text>
      </g>
      <g stroke="#0592cd" stroke-width="2" opacity=".5">
        <line x1="0" y1="-133" x2="0" y2="-300" transform="rotate(30)"/>
        <line x1="0" y1="-133" x2="0" y2="-300" transform="rotate(90)"/>
        <line x1="0" y1="-133" x2="0" y2="-300" transform="rotate(150)"/>
        <line x1="0" y1="-133" x2="0" y2="-300" transform="rotate(210)"/>
        <line x1="0" y1="-133" x2="0" y2="-300" transform="rotate(270)"/>
        <line x1="0" y1="-133" x2="0" y2="-300" transform="rotate(330)"/>
      </g>
      <g fill="#9fd0ec" role="img" aria-label="Six blue anatomical figures showing head, neck and back pain points">
        <ellipse cx="0" cy="-215" rx="62" ry="70"/>
        <ellipse cx="186" cy="-108" rx="62" ry="70"/>
        <ellipse cx="186" cy="108" rx="62" ry="70"/>
        <ellipse cx="0" cy="215" rx="62" ry="70"/>
        <ellipse cx="-186" cy="108" rx="62" ry="70"/>
        <ellipse cx="-186" cy="-108" rx="62" ry="70"/>
      </g>
      <circle r="133" fill="url(#core)" stroke="#fff" stroke-width="4"/>
      <g fill="#fff" font-family="Open Sans, Arial, sans-serif" font-weight="700" text-anchor="middle">
        <text y="-58" font-size="25">Do You</text>
        <text y="-26" font-size="25">Suffer From Any</text>
        <text y="6" font-size="25">of the Following</text>
        <text y="98" font-size="88">?</text>
      </g>
      <line x1="-100" y1="22" x2="100" y2="22" stroke="#fff" stroke-width="2"/>
    </g>
  </svg>
  <div class="ready">
    <h2>Are You Ready to Feel Better?</h2>
    <div class="rule"></div>
    <p>Lorem ipsum dolor sit amet, nostra in aliquet arcu leo eu, aliquet integer sed leo blandit, vivamus sollicitudin vel sagittis. Nesciunt nunc eu aliquet sodales enim scelerisque, explicabo amet quis. Amet tempor cras vitae, amet et ante. Consequat libero odio, lorem bibendum, pellentesque congue. Malesuada amet, amet nibh nulla justo mattis imperdiet in, wisi vero nibh incidunt posuere ligula, quibusdam sodales.</p>
    <p class="quote">Lorem ipsum dolor sit amet, nostra in aliquet arcu leo eu, aliquet integer sed leo blandit, vivamus sollicitudin vel sagittis. Nesciunt nunc eu aliquet sodales enim scelerisque, explicabo amet quis. Amet tempor cras vitae, amet et ante mattis imperdiet in, wisi vero nibh incidunt posuere ligula, quibusdam sodales.</p>
    <p class="quote">Lorem ipsum dolor sit amet, nostra in aliquet arcu leo eu, aliquet integer sed leo blandit, vivamus sollicitudin vel sagittis. Nesciunt nunc eu aliquet sodales enim scelerisque, explicabo amet quis. Amet tempor cras vitae, amet et ante mattis imperdiet in, wisi vero nibh incidunt posuere ligula, quibusdam sodales.</p>
    <div class="cta"><span class="btn">CALL US</span></div>
  </div>
</section>

<section class="expect">
  <div class="expect-band"></div>
  <h2>What to Expect</h2>
  <div class="rule-w"></div>
  <article class="visit" style="left:69px"><div class="ph" role="img" aria-label="Doctor in a white coat at a lab bench" style="background:linear-gradient(160deg,#e8f1f6,#9fc3d8)"></div><div class="tag">Visit 1</div><p>Lorem ipsum dolor sit amet, sagittis iure in magna libero nunc, maecenas quia diam at sed, enim dui, mauris ut dignissim cras enim egestas.</p></article>
  <article class="visit" style="left:338px"><div class="ph" role="img" aria-label="Doctor reviewing an x-ray film" style="background:linear-gradient(160deg,#cfe3ef,#5f8fb0)"></div><div class="tag">Visit 2</div><p>Lorem ipsum dolor sit amet, sagittis iure in magna libero nunc, maecenas quia diam at sed, enim dui, mauris ut dignissim cras enim egestas.</p></article>
  <article class="visit" style="left:610px"><div class="ph" role="img" aria-label="Practitioner adjusting a patient's neck" style="background:linear-gradient(160deg,#eef0f2,#c9b8a8)"></div><div class="tag">Visit 3</div><p>Lorem ipsum dolor sit amet, sagittis iure in magna libero nunc, maecenas quia diam at sed, enim dui, mauris ut dignissim cras enim egestas.</p></article>
  <article class="visit" style="left:881px"><div class="ph" role="img" aria-label="Relaxed woman receiving a head massage" style="background:linear-gradient(160deg,#f3e4d6,#c99e80)"></div><div class="tag">Visit 4</div><p>Lorem ipsum dolor sit amet, sagittis iure in magna libero nunc, maecenas quia diam at sed, enim dui, mauris ut dignissim cras enim egestas.</p></article>
</section>

<section class="testimonials">
  <div class="sea" role="img" aria-label="Calm blue sea under a bright sky"></div>
  <h2>Testimonials</h2>
  <div class="rule-w"></div>
  <div class="quote-box">
    <span class="qmark" style="left:12px;top:6px">“</span>
    <p>Lorem Ipsum is simply dummy text of the printing and typesetting industry. Lorem Ipsum has been the industry's standard dummy text ever since the 1500s, when an unknown printer took a galley of type and scrambled it to make a type specimen book. It has survived not only five centuries, but also the leap into electronic typesetting, remaining essentially unchanged. It was popularised in the 1960s with the release of sheets containing Lorem Ipsum passages, and more recently with desktop publishing software including versions of Lorem Ipsum.</p>
    <div class="portrait" role="img" aria-label="Portrait of a smiling client" style="background:linear-gradient(160deg,#e9dccf,#b89a85)"></div>
    <span class="qmark" style="left:660px;top:180px">”</span>
    <div class="who">Dana Whitfield</div>
  </div>
  <div class="t-arrow" style="left:119px"></div>
  <div class="t-arrow" style="left:906px"></div>
</section>

<section class="blog">
  <h2>Blog Posts</h2>
  <div class="rule-b"></div>
  <div class="b-arrow" style="left:22px"></div>
  <div class="b-arrow" style="left:1144px"></div>
  <article class="post" style="left:69px"><div class="ph" role="img" aria-label="Group yoga class on mats" style="background:linear-gradient(160deg,#e8eef2,#8fb3c9)"></div><div class="body"><h3>Headline Example 1</h3><p>Lorem ipsum dolor sit amet, mus non convallis turpis a, sed sollicitudin quisquam wisi lectus proin ...</p><span class="more">Read more</span></div></article>
  <article class="post" style="left:432px"><div class="ph" role="img" aria-label="Doctor talking with an older patient" style="background:linear-gradient(160deg,#dfe6ea,#a3b4bd)"></div><div class="body"><h3>Headline Example 2</h3><p>Lorem ipsum dolor sit amet, mus non convallis turpis a, sed sollicitudin quisquam wisi lectus proin ...</p><span class="more">Read more</span></div></article>
  <article class="post" style="left:795px"><div class="ph" role="img" aria-label="Woman exercising on a gym bike" style="background:linear-gradient(160deg,#d9d9d9,#6d6d6d)"></div><div class="body"><h3>Headline Example 3</h3><p>Lorem ipsum dolor sit amet, mus non convallis turpis a, sed sollicitudin quisquam wisi lectus proin ...</p><span class="more">Read more</span></div></article>
</section>

<footer class="footer">
  <h4 style="left:104px">Recent Posts</h4>
  <ul>
    <li>Sonsectetur Sedipiscing Elit</li>
    <li>Fed do Eiusmod Tempor</li>
    <li>Incididunt ut Labore et Dolore</li>
    <li>Nostrud Exercitation Ullameo</li>
    <li>Magna Aliqua</li>
  </ul>
  <div class="sep" style="left:416px"></div>
  <h4 style="left:470px">Contact</h4>
  <div class="contact">
    <div><svg width="16" height="20" viewBox="0 0 16 20"><path d="M8 0a7 7 0 0 0-7 7c0 5 7 13 7 13s7-8 7-13a7 7 0 0 0-7-7zm0 10a3 3 0 1 1 0-6 3 3 0 0 1 0 6z" fill="#9bcb3c"/></svg>48 Placid Grove Lane<br>Alder Falls, MD 20999</div>
    <div><svg width="16" height="16" viewBox="0 0 16 16"><path d="M3 1l3 3-2 2c1 2 3 4 5 5l2-2 3 3-2 3C7 15 1 9 1 3z" fill="#9bcb3c"/></svg>555 - 018 - 4420</div>
    <div><svg width="18" height="14" viewBox="0 0 18 14"><rect x="0" y="0" width="18" height="14" rx="2" fill="#9bcb3c"/><path d="M1 1l8 7 8-7" stroke="#1f1f1f" stroke-width="1.5" fill="none"/></svg>hello@fernwell.example</div>
  </div>
  <div class="sep" style="left:776px"></div>
  <h4 style="left:826px">Our Location</h4>
  <div class="map" role="img" aria-label="Street map showing the clinic location"></div>
</footer>
<div class="copy">Copyright 2017 - Fernwell Medical Clinic</div>

</body>
</html>
```